Maplecrest Disability - Social Security Disability Attorneys

Our company is expanding to attract clients nationwide for our social security disability practice. We have a logo, but I am looking for a creative and elegant letterhead that projects an image of being technologically advanced but still professional enough for the legal field. I am looking for the "wow factor" combined with this is still professional enough for a law practice.

Requesting letterhead and business card design
Updates

Had to update and change the logo. The previous logo had a typo. Please send updates with the new logo for consideration. The letterhead and business cards should be professional enough to be used for a law firm. Thanks.

Industry/Entity Type

Law Practice, Law Firm, Healthcare Industry, Government

Colors

Designer to choose colors to be used in the design.

Requirements
Nice to have
• **Please create a vertical design for the business card**

```html
<!DOCTYPE html>
<html lang="en">
<head>
<meta charset="utf-8">
<title>Maplecrest Disability – Business Card</title>
<link rel="stylesheet" href="https://fonts.googleapis.com/css2?family=Libre+Baskerville:wght@700&family=Mulish:wght@400&display=swap">
<style>
  :root {
    --brand-blue: #4166d5;
    --brand-orange: #f07e2a;
    --card-white: #f7f7f7;
    --backdrop: #dcdcdc;
    --text-light: #ffffff;
  }
  * { margin: 0; padding: 0; box-sizing: border-box; }
  html, body { width: 1200px; height: 1200px; overflow: hidden; background: var(--backdrop); }
  .canvas { position: relative; width: 1200px; height: 1200px; }

  .card {
    position: absolute;
    left: 257px;
    width: 686px;
    height: 392px;
    border-radius: 22px;
    overflow: hidden;
  }
  .card--front { top: 165px; background: var(--card-white); }
  .card--back { top: 653px; background: var(--brand-blue); }

  /* front */
  .front-top { position: absolute; left: 0; top: 0; width: 100%; height: 240px; }
  .wordmark { position: absolute; left: 46px; top: 112px; }
  .wordmark-name {
    font-family: "Mulish", sans-serif; font-weight: 400;
    font-size: 24px; letter-spacing: 0.5px; color: var(--brand-blue); line-height: 1;
  }
  .wordmark-tagline {
    font-family: "Mulish", sans-serif; font-weight: 400;
    font-size: 9px; letter-spacing: 1.2px; color: var(--brand-blue); margin-top: 7px;
  }
  .horizon-line {
    position: absolute; left: 0; top: 240px; width: 100%; height: 5px;
    background: var(--brand-orange);
  }
  .front-bottom {
    position: absolute; left: 0; top: 250px; width: 100%; height: 142px;
    background: var(--brand-blue); color: var(--text-light);
  }
  .person { position: absolute; left: 42px; top: 24px; }
  .person-name {
    font-family: "Libre Baskerville", serif; font-weight: 700;
    font-size: 23px; letter-spacing: 0.3px; line-height: 1.1;
  }
  .person-role { font-family: "Mulish", sans-serif; font-size: 18px; margin-top: 2px; }
  .person-address { font-family: "Mulish", sans-serif; font-size: 15px; line-height: 19px; margin-top: 8px; }

  .contact { position: absolute; right: 34px; top: 38px; list-style: none; }
  .contact li {
    display: flex; align-items: center; justify-content: flex-end; gap: 8px;
    font-family: "Mulish", sans-serif; font-size: 15px; line-height: 19.5px;
  }
  .contact svg { width: 14px; height: 14px; fill: var(--text-light); flex: none; }

  /* back */
  .back-wordmark {
    position: absolute; left: 0; top: 0; width: 100%; height: 100%;
    display: flex; flex-direction: column; align-items: center; justify-content: center;
    padding-top: 60px;
  }
  .back-name {
    font-family: "Mulish", sans-serif; font-weight: 400; font-size: 34px;
    letter-spacing: 1px; color: var(--text-light); line-height: 1;
  }
  .back-tagline {
    font-family: "Mulish", sans-serif; font-weight: 400; font-size: 11px;
    letter-spacing: 2px; color: var(--text-light); margin-top: 12px;
  }
</style>
</head>
<body>
<main class="canvas">

  <section class="card card--front" aria-label="Business card front">
    <div class="front-top">
      <div class="wordmark">
        <div class="wordmark-name">Maplecrest Disability</div>
        <div class="wordmark-tagline">Social Security Disability Attorneys</div>
      </div>
    </div>
    <div class="horizon-line"></div>
    <div class="front-bottom">
      <div class="person">
        <div class="person-name">DANIEL WHITFORD</div>
        <div class="person-role">Founder &amp; CEO</div>
        <div class="person-address">214 Larkspur Avenue<br>Anchorage, Alaska 99501</div>
      </div>
      <ul class="contact">
        <li>936-555-0147
          <svg viewBox="0 0 24 24" aria-hidden="true"><path d="M6.6 10.8a15.1 15.1 0 0 0 6.6 6.6l2.2-2.2a1 1 0 0 1 1-.25 11.4 11.4 0 0 0 3.6.57 1 1 0 0 1 1 1V20a1 1 0 0 1-1 1A17 17 0 0 1 3 4a1 1 0 0 1 1-1h3.5a1 1 0 0 1 1 1c0 1.25.2 2.45.57 3.57a1 1 0 0 1-.25 1z"/></svg>
        </li>
        <li>936-555-0183
          <svg viewBox="0 0 24 24" aria-hidden="true"><path d="M7 1h10a2 2 0 0 1 2 2v18a2 2 0 0 1-2 2H7a2 2 0 0 1-2-2V3a2 2 0 0 1 2-2zm0 3v15h10V4z"/></svg>
        </li>
        <li>info@maplecrestdisability.com
          <svg viewBox="0 0 24 24" aria-hidden="true"><path d="M2 5h20v14H2zm2 2v.5l8 5 8-5V7zm0 2.8V17h16V9.8l-8 5z"/></svg>
        </li>
        <li>www.maplecrestdisability.com
          <svg viewBox="0 0 24 24" aria-hidden="true"><path d="M12 2a10 10 0 1 0 0 20 10 10 0 0 0 0-20zm-1 17.9A8 8 0 0 1 4.2 10.2L9 15v1a2 2 0 0 0 2 2zm6.9-2.5A2 2 0 0 0 16 16h-1v-3a1 1 0 0 0-1-1H8v-2h2a1 1 0 0 0 1-1V7h2a2 2 0 0 0 2-2v-.4a8 8 0 0 1 2.9 12.8z"/></svg>
        </li>
      </ul>
    </div>
  </section>

  <section class="card card--back" aria-label="Business card back">
    <div class="back-wordmark">
      <div class="back-name">Maplecrest Disability</div>
      <div class="back-tagline">Social Security Disability Attorneys</div>
    </div>
  </section>

</main>
</body>
</html>
```